Business Card Design

We need a business card designed for our new company. Prefer a black card with white logo & writing.

Contact Information for Business Card

Ted Galloway, address: 7-4812 Fernhollow Road, Abbotsford, BC, V3K 8R2, Office Phone: 604-712-3390, Cell: 604-947-2164, Email: ted@resinworkshub.ca

Colors

Designer to choose only greyscale colors for use in the design.

```html
<!DOCTYPE html>
<html lang="en">
<head>
<meta charset="utf-8">
<title>Resinworks Hub – Business Card</title>
<link href="https://fonts.googleapis.com/css2?family=Lato:wght@300;400&family=Montserrat:wght@700&display=swap" rel="stylesheet">
<style>
  :root {
    --backdrop: #3a3a3a;
    --card: #1f1f1f;
    --ink: #ffffff;
    --ink-soft: #e6e6e6;
  }
  * { box-sizing: border-box; margin: 0; padding: 0; }
  html, body {
    width: 1200px; height: 895px; overflow: hidden;
    background: var(--backdrop);
  }
  .canvas {
    position: relative; width: 1200px; height: 895px;
    display: flex; flex-direction: column; align-items: center; justify-content: center; gap: 56px;
  }
  .card {
    position: relative; width: 630px; height: 360px;
    background: var(--card); border-radius: 22px;
    color: var(--ink);
    box-shadow: 0 10px 28px rgba(0,0,0,.35);
    overflow: hidden;
  }
  .wordmark {
    display: flex; align-items: center; gap: 12px;
    font-family: "Montserrat", sans-serif; font-weight: 700;
    color: var(--ink); line-height: 1; letter-spacing: .5px;
    white-space: nowrap;
  }
  .wordmark__mark { background: var(--ink); border-radius: 50%; flex: none; }

  /* Front */
  .card--front { display: flex; align-items: center; justify-content: center; }
  .card--front .wordmark { font-size: 44px; }
  .card--front .wordmark__mark { width: 26px; height: 26px; }

  /* Back */
  .card--back .wordmark { position: absolute; left: 50px; top: 150px; font-size: 25px; }
  .card--back .wordmark__mark { width: 16px; height: 16px; }
  .person { position: absolute; right: 44px; top: 38px; text-align: right; }
  .person__name { font-family: "Montserrat", sans-serif; font-weight: 700; font-size: 26px; }
  .person__title { font-family: "Lato", sans-serif; font-weight: 300; font-size: 20px; margin-top: 2px; }
  .rule { position: absolute; height: 1px; background: var(--ink); }
  .rule--top { right: 36px; top: 112px; width: 300px; }
  .rule--bottom { left: 40px; top: 252px; width: 290px; }
  .address {
    position: absolute; right: 44px; top: 150px; text-align: right;
    font-family: "Lato", sans-serif; font-size: 19px; line-height: 1.55; color: var(--ink-soft);
  }
  .contacts {
    position: absolute; left: 48px; top: 264px; list-style: none;
    font-family: "Lato", sans-serif; font-size: 17px; color: var(--ink-soft);
  }
  .contacts li { display: flex; align-items: center; gap: 12px; height: 27px; }
  .contacts svg { width: 16px; height: 16px; flex: none; }
</style>
</head>
<body>
<main class="canvas">
  <section class="card card--front" aria-label="Card front">
    <div class="wordmark"><span class="wordmark__mark"></span>Resinworks Hub</div>
  </section>

  <section class="card card--back" aria-label="Card back">
    <div class="wordmark"><span class="wordmark__mark"></span>Resinworks Hub</div>

    <div class="person">
      <p class="person__name">Ted Galloway</p>
      <p class="person__title">President</p>
    </div>
    <span class="rule rule--top"></span>

    <p class="address">7-4812 Fernhollow Road,<br>Abbotsford, BC, V3K 8R2,</p>

    <span class="rule rule--bottom"></span>
    <ul class="contacts">
      <li>
        <svg viewBox="0 0 24 24" aria-hidden="true"><path fill="#fff" d="M6.6 10.8a15.5 15.5 0 0 0 6.6 6.6l2.2-2.2c.3-.3.7-.4 1-.2 1.1.4 2.3.6 3.6.6.6 0 1 .4 1 1V20c0 .6-.4 1-1 1A17 17 0 0 1 3 4c0-.6.4-1 1-1h3.5c.6 0 1 .4 1 1 0 1.3.2 2.5.6 3.6.1.3 0 .7-.2 1z"/></svg>
        604-712-3390
      </li>
      <li>
        <svg viewBox="0 0 24 24" aria-hidden="true"><rect x="6" y="2" width="12" height="20" rx="2" fill="none" stroke="#fff" stroke-width="1.8"/><circle cx="12" cy="18.5" r="1" fill="#fff"/></svg>
        604-947-2164
      </li>
      <li>
        <svg viewBox="0 0 24 24" aria-hidden="true"><rect x="2" y="5" width="20" height="14" fill="none" stroke="#fff" stroke-width="1.8"/><path d="M2 5l10 8 10-8" fill="none" stroke="#fff" stroke-width="1.8"/></svg>
        ted@resinworkshub.ca
      </li>
    </ul>
  </section>
</main>
</body>
</html>
```